July 2022 Industrial Manufacturer Product Expo Mexico City

We manufacture large screws and fastners for large Mining equipment, Trains, large ships, airplanes, wind turbines, and so on. We also do custom work base on the customer needs. No matter the size we can make it.
We have a Expo coming up with companies all over the world. We have to stand out we are a family own business so our customer service will be above and beyond anyone can provide. We do not have a sales force to push our products and services we provide one on one service.
Plus@!! I'm looking for anything that you designers can come up with if it was your company to put on a business card, plus i want to do a 1 or 2 sided pamphlet, and then a website. We make Speciality Bolts for large mining equipment these bolts can be 3 to 4 foot long!!! Plus fasteners, Nuts, washers, any, size, strengths, special materials, we offer more of a ono on one customer service, We are a small company, family own, but can fulfill any type of orders. We can also provide special time lines for emergency orders. "We keep the machines running we here at KRV don't believe in down time" We want to hear any slogan based on our company to stand out.
Thanks i really appreciate all your work and options that we have to pick on. Plus just a thought we could possibly want to entertain a experience Marketing internet help maybe a employment possibility. Thanks

I need 2 cards one in Spanish and English Like the steel back ground maybe send me in some bright red and blue writing Same with the Black cards Please remove the word Military The logo KRV maybe integrate a picture of a Bolt 🔩 Thank you

Still looking for I need 2 cards one in Spanish and English Like the steel back ground maybe send me in some bright red and blue writing Same with the Black cards try bright writing Please remove the word Military The logo KRV maybe integrate a picture of a Bolt 🔩 Plus will need the company to make a brochure and website next Thank you

Target Market(s)

Large Mining, Ship, Train, Green Energy, VELM, and Government equipment. Throughout the World

Industry/Entity Type

We can Custom Manufacture any type of Fastners for Mining equipment, Trains, Ships, Green energy, Governments, or military projects. wind turbines,

Contact Information for Business Card

I attached the name and contact info that's on a card, plus the Company Logo. Would like industrial looking background with Bright Colors that will stand out!! If we can insert somewhere maybe on back that we "Custom Manufacture Any Size or Quantity Fastners for Large Mining Equipment, Trains, Ships, Green Energy Equipment or Government Projects

Font styles to use
Other font styles liked:
• You Pick, has to be bold, colorful standout, Professional looking Beable to read it.

Colors

Designer to choose colors to be used in the design.

Requirements
Must have
• Need in Spanish and English TO STANDOUT FROM THE REST OF THE EXPO!! See Business card details, Rounded corners
Nice to have
• Can i see some of the darker cards with Bright Red and Blue letters I like to see the different type of card material, heavy thickness, plastic, transparent, Metal types, Bright Colors, I saw like Raised letters like on the logo.

```html
<!DOCTYPE html>
<html lang="es">
<head>
<meta charset="utf-8">
<title>KRV Business Card</title>
<link rel="stylesheet" href="https://fonts.googleapis.com/css2?family=Tinos&family=Cinzel:wght@600&display=swap">
<style>
  :root {
    --backdrop: #262626;
    --card-white: #ffffff;
    --name-blue: #1a8fd0;
    --ink-navy: #1b1f78;
    --icon-blue: #0b5fb0;
    --rule-grey: #6b6b6b;
    --grad-top: #0094d6;
    --grad-bottom: #001f80;
    --text-light: #ffffff;
  }
  html, body {
    margin: 0;
    padding: 0;
    width: 1065px;
    height: 1200px;
    overflow: hidden;
    background: var(--backdrop);
  }
  .canvas {
    position: relative;
    width: 1065px;
    height: 1200px;
    background: var(--backdrop);
  }
  .card {
    position: absolute;
    filter: drop-shadow(3px 3px 2px rgba(0,0,0,0.85));
  }
  .card-front {
    left: 292px;
    top: 218px;
    width: 583px;
    height: 362px;
    background: var(--card-white);
    border-radius: 0 181px 181px 0;
  }
  .card-back {
    left: 263px;
    top: 623px;
    width: 582px;
    height: 363px;
    background: linear-gradient(to bottom, var(--grad-top) 0%, #0070bd 40%, var(--grad-bottom) 100%);
    border-radius: 181px 0 0 181px;
  }
  .brand-name {
    position: absolute;
    left: 84px;
    top: 164px;
    width: 60px;
    text-align: center;
    font-family: "Tinos", "Times New Roman", serif;
    font-size: 26px;
    line-height: 30px;
    color: var(--icon-blue);
    letter-spacing: 1px;
  }
  .divider {
    position: absolute;
    left: 164px;
    top: 112px;
    width: 1px;
    height: 147px;
    background: var(--rule-grey);
  }
  .contact {
    position: absolute;
    left: 183px;
    font-family: "Tinos", "Times New Roman", serif;
    white-space: nowrap;
  }
  .contact-name {
    top: 108px;
    font-size: 22.5px;
    line-height: 26px;
    color: var(--name-blue);
  }
  .contact-quotes {
    top: 157px;
    font-size: 16.5px;
    line-height: 22px;
    color: var(--ink-navy);
  }
  .contact-phone {
    font-size: 17.5px;
    line-height: 20px;
    color: var(--ink-navy);
    display: flex;
    align-items: center;
    gap: 10px;
  }
  .phone-office { top: 219px; }
  .phone-mobile { top: 240px; }
  .contact-phone svg { width: 14px; height: 14px; flex: none; }
  .services {
    position: absolute;
    left: 0;
    right: 0;
    top: 127px;
    margin: 0;
    padding: 0;
    list-style: none;
    text-align: center;
    font-family: "Cinzel", "Times New Roman", serif;
    font-weight: 600;
    font-size: 18px;
    line-height: 26.5px;
    color: var(--text-light);
    letter-spacing: 0.3px;
  }
</style>
</head>
<body>
<main class="canvas">
  <section class="card card-front" aria-label="Front of card">
    <div class="brand-name">KRV</div>
    <div class="divider"></div>
    <div class="contact contact-name">Lic. Daniela Moreno Ibarra Soto</div>
    <div class="contact contact-quotes">Cotizaciones en<br>krvtornilleria.ventas@gmail.com</div>
    <div class="contact contact-phone phone-office">
      <svg viewBox="0 0 24 24" aria-hidden="true"><path fill="var(--icon-blue)" d="M6.6 2.5l3 3.2-1.8 2.6c1.2 2.6 3.2 4.7 5.8 6l2.6-1.8 3.3 3-1.6 3.4c-.5.6-1.3.9-2.1.7C9.4 18 4.7 13.3 3.4 6.9c-.2-.8.1-1.6.7-2.1z"/><path fill="none" stroke="var(--icon-blue)" stroke-width="2" d="M13 6a5 5 0 0 1 5 5M13 2a9 9 0 0 1 9 9"/></svg>
      <span>8714405218</span>
    </div>
    <div class="contact contact-phone phone-mobile">
      <svg viewBox="0 0 24 24" aria-hidden="true"><rect x="5" y="2" width="14" height="20" rx="2" fill="none" stroke="var(--icon-blue)" stroke-width="2.4"/><circle cx="12" cy="18" r="1.4" fill="var(--icon-blue)"/></svg>
      <span>8716632094</span>
    </div>
  </section>

  <section class="card card-back" aria-label="Back of card">
    <ul class="services">
      <li>Custom Manufacture Any Size or Quantity</li>
      <li>Fastners for Large&nbsp; Mining Equipment</li>
      <li>Trains, Ships, Green Energy Equipment</li>
      <li>or Government Projects</li>
    </ul>
  </section>
</main>
</body>
</html>
```